Circle of services Brelwood Data Works IT Services

Update a graphic we use to describe our services with new icons, change a few descriptions.
1. Please replace all icons with new crisp icons (similar is fine).

2. Delete:
Global Device Monitoring
Security Management
Cloud Services (Iaas, Saas, Paas)

3. Add:
Training
IT Security
Cloud Services

Thank you.

Target Market(s)

Small businesses and professional service organizations

Industry/Entity Type

It Professional

Font styles to use
Other font styles liked:
• Nexa Bold Sans Serif

Requirements
Must have
• Good crisp graphics. Need to deliver ai file
Nice to have
• Good colors easy to read
Should not have
• Nothing too fancy

```html
<!DOCTYPE html>
<html lang="en">
<head>
<meta charset="utf-8">
<title>Brelwood Data Works – Circle of Services</title>
<link href="https://fonts.googleapis.com/css2?family=Poppins:wght@500;600;700&display=swap" rel="stylesheet">
<style>
  :root {
    --bg-center: #ffffff;
    --bg-edge: #e9ebee;
    --blue: #0aa7e6;
    --blue-light: #45c6f1;
    --blue-deep: #0a6fdc;
    --icon: #1aa3e4;
    --label: #33373a;
    --brand-dark: #464b4f;
    --disk-grey: #e5e6e9;
    --shadow-grey: #b4b5b7;
    --white: #ffffff;
  }
  html, body {
    margin: 0;
    padding: 0;
    width: 1200px;
    height: 1200px;
    overflow: hidden;
  }
  .canvas {
    width: 1200px;
    height: 1200px;
    background: radial-gradient(circle at 50% 50%, var(--bg-center) 0%, #f4f5f7 45%, var(--bg-edge) 100%);
  }
  .services-wheel { display: block; }
  .ring { fill: none; stroke: var(--blue); stroke-width: 10; }
  .spoke { stroke: var(--blue); stroke-width: 8; }
  .joint { fill: var(--blue); }
  .node-face { fill: var(--white); }
  .icon { fill: none; stroke: var(--icon); stroke-width: 1.7; stroke-linecap: round; stroke-linejoin: round; }
  .label {
    font-family: "Poppins", sans-serif;
    font-weight: 500;
    font-size: 12.5px;
    fill: var(--label);
    text-anchor: middle;
  }
  .brand-name {
    font-family: "Poppins", sans-serif;
    font-weight: 600;
    fill: var(--brand-dark);
    text-anchor: middle;
  }
  .brand-mark { fill: var(--blue); }
</style>
</head>
<body>
<div class="canvas">
<svg class="services-wheel" width="1200" height="1200" viewBox="0 0 1200 1200" xmlns="http://www.w3.org/2000/svg">
  <defs>
    <linearGradient id="node-rim" x1="0" y1="0" x2="1" y2="1">
      <stop offset="0" stop-color="#3aa0ea"/>
      <stop offset="0.45" stop-color="#17b3ec"/>
      <stop offset="0.75" stop-color="#0a8ee4"/>
      <stop offset="1" stop-color="#0a62d6"/>
    </linearGradient>
    <linearGradient id="disk-fill" x1="0" y1="0" x2="1" y2="1">
      <stop offset="0" stop-color="#dfe1e5"/>
      <stop offset="1" stop-color="#f2f3f5"/>
    </linearGradient>
    <linearGradient id="long-shadow" x1="0" y1="0" x2="1" y2="1">
      <stop offset="0" stop-color="#9d9ea0"/>
      <stop offset="1" stop-color="#d6d7d9"/>
    </linearGradient>
    <clipPath id="disk-clip"><circle cx="600" cy="607" r="214"/></clipPath>
    <filter id="soft" x="-20%" y="-20%" width="140%" height="140%">
      <feDropShadow dx="0" dy="2" stdDeviation="3" flood-color="#0a4f9a" flood-opacity="0.15"/>
    </filter>
  </defs>

  <!-- centre disk with long shadow -->
  <g class="hub">
    <circle cx="600" cy="607" r="214" fill="url(#disk-fill)"/>
    <g clip-path="url(#disk-clip)">
      <polygon points="714,488 480,722 780,1022 1014,788" fill="url(#long-shadow)"/>
    </g>
    <circle cx="597" cy="605" r="166" fill="var(--white)"/>
    <circle class="brand-mark" cx="597" cy="560" r="36"/>
    <text class="brand-name" x="597" y="638" font-size="30">Brelwood</text>
    <text class="brand-name" x="597" y="672" font-size="30">Data Works</text>
  </g>

  <!-- ring and spokes -->
  <circle class="ring" cx="600" cy="606" r="266"/>
  <g class="spokes">
    <line class="spoke" x1="594" y1="342" x2="594" y2="222"/>
    <line class="spoke" x1="738" y1="383" x2="801" y2="281"/>
    <line class="spoke" x1="837" y1="495" x2="949" y2="447"/>
    <line class="spoke" x1="862" y1="643" x2="981" y2="663"/>
    <line class="spoke" x1="795" y1="781" x2="891" y2="859"/>
    <line class="spoke" x1="669" y1="862" x2="708" y2="977"/>
    <line class="spoke" x1="520" y1="858" x2="489" y2="977"/>
    <line class="spoke" x1="398" y1="776" x2="308" y2="858"/>
    <line class="spoke" x1="337" y1="643" x2="219" y2="665"/>
    <line class="spoke" x1="355" y1="497" x2="247" y2="438"/>
    <line class="spoke" x1="453" y1="385" x2="385" y2="281"/>
  </g>
  <g class="joints">
    <circle class="joint" cx="594" cy="342" r="13"/>
    <circle class="joint" cx="738" cy="383" r="13"/>
    <circle class="joint" cx="837" cy="495" r="13"/>
    <circle class="joint" cx="862" cy="643" r="13"/>
    <circle class="joint" cx="795" cy="781" r="13"/>
    <circle class="joint" cx="669" cy="862" r="13"/>
    <circle class="joint" cx="520" cy="858" r="13"/>
    <circle class="joint" cx="398" cy="776" r="13"/>
    <circle class="joint" cx="337" cy="643" r="13"/>
    <circle class="joint" cx="355" cy="497" r="13"/>
    <circle class="joint" cx="453" cy="385" r="13"/>
  </g>

  <!-- Remote Help Desk -->
  <g class="service-node" transform="translate(594 222)">
    <circle r="78" fill="url(#node-rim)" filter="url(#soft)"/>
    <circle class="node-face" r="60"/>
    <g class="icon" transform="translate(0 -22)">
      <circle cx="0" cy="-8" r="9"/>
      <path d="M-12 -8 a12 12 0 0 1 24 0"/>
      <rect x="-14" y="-10" width="4" height="7" rx="2"/>
      <rect x="10" y="-10" width="4" height="7" rx="2"/>
      <path d="M12 -3 q0 8 -8 8 h-3"/>
      <path d="M-20 20 q2 -14 20 -15 q18 1 20 15 z"/>
      <path d="M-4 6 l4 5 l4 -5 M0 11 v9"/>
    </g>
    <text class="label" x="0" y="25">Remote Help</text>
    <text class="label" x="0" y="40">Desk</text>
  </g>

  <!-- Data Collection & Reporting -->
  <g class="service-node" transform="translate(801 281)">
    <circle r="78" fill="url(#node-rim)" filter="url(#soft)"/>
    <circle class="node-face" r="60"/>
    <g class="icon" transform="translate(0 -20)">
      <rect x="-20" y="-14" width="40" height="30" rx="1"/>
      <path d="M-16 -14 v-6 h32 v6 M-12 -20 v-4 h24 v4"/>
      <rect x="-12" y="-6" width="24" height="16"/>
      <circle cx="-6" cy="-1" r="2.5"/>
      <path d="M-10 7 q4 -6 8 0 M2 -3 h7 M2 1 h7 M2 5 h5"/>
    </g>
    <text class="label" x="0" y="20">Data Collection</text>
    <text class="label" x="0" y="35">&amp; Reporting</text>
  </g>

  <!-- Desktop Support -->
  <g class="service-node" transform="translate(949 447)">
    <circle r="78" fill="url(#node-rim)" filter="url(#soft)"/>
    <circle class="node-face" r="60"/>
    <g class="icon" transform="translate(0 -18)">
      <rect x="-24" y="-16" width="32" height="22" rx="1"/>
      <path d="M-24 2 h32 M-8 6 v6 M-14 12 h12"/>
      <rect x="12" y="-18" width="12" height="32" rx="1"/>
      <circle cx="18" cy="-10" r="2"/>
      <path d="M15 2 h6 M15 6 h6 M15 10 h6"/>
    </g>
    <text class="label" x="0" y="28">Desktop Support</text>
  </g>

  <!-- Core IT Services -->
  <g class="service-node" transform="translate(981 663)">
    <circle r="78" fill="url(#node-rim)" filter="url(#soft)"/>
    <circle class="node-face" r="60"/>
    <g class="icon" transform="translate(0 -31)">
      <rect x="-18" y="-16" width="36" height="26" rx="1"/>
      <path d="M-24 10 h48 v3 q0 2 -2 2 h-44 q-2 0 -2 -2 z"/>
      <path d="M-7 -3 a7 7 0 0 1 12 -4 M7 -3 a7 7 0 0 1 -12 4"/>
      <path d="M5 -10 v3 h-3 M-5 4 v-3 h3"/>
    </g>
    <text class="label" x="0" y="1">Core IT Services</text>
    <text class="label" x="0" y="16">DNS/DHCP,</text>
    <text class="label" x="0" y="31">Email etc</text>
  </g>

  <!-- Cloud Services -->
  <g class="service-node" transform="translate(891 859)">
    <circle r="78" fill="url(#node-rim)" filter="url(#soft)"/>
    <circle class="node-face" r="60"/>
    <g class="icon" transform="translate(0 -22)">
      <path d="M-18 2 a8 8 0 0 1 2 -15 a12 12 0 0 1 22 -4 a9 9 0 0 1 12 11 a7 7 0 0 1 0 8"/>
      <rect x="-8" y="0" width="16" height="6"/>
      <rect x="-8" y="7" width="16" height="6"/>
      <rect x="-8" y="14" width="16" height="6"/>
      <path d="M-4 0 v-8 M0 0 v-13 M4 0 v-8"/>
      <circle cx="-4" cy="-10" r="1.5"/><circle cx="0" cy="-15" r="1.5"/><circle cx="4" cy="-10" r="1.5"/>
    </g>
    <text class="label" x="0" y="33">Cloud Services</text>
  </g>

  <!-- IT Security -->
  <g class="service-node" transform="translate(708 977)">
    <circle r="78" fill="url(#node-rim)" filter="url(#soft)"/>
    <circle class="node-face" r="60"/>
    <g class="icon" transform="translate(0 -22)">
      <path d="M-6 -22 l-10 4 v7 q0 8 10 12 q10 -4 10 -12 v-7 z"/>
      <path d="M-10 -12 l3 3 l6 -6"/>
      <ellipse cx="12" cy="-18" rx="8" ry="3"/>
      <path d="M4 -18 v12 q8 4 16 0 v-12 M4 -12 q8 4 16 0"/>
      <path d="M-6 1 v5 M-18 6 h26 M-18 6 v4 M-6 6 v4 M8 6 v4"/>
      <rect x="-23" y="10" width="10" height="7"/>
      <rect x="-11" y="10" width="10" height="7"/>
      <rect x="3" y="10" width="10" height="7"/>
      <path d="M-18 17 v3 M-6 17 v3 M8 17 v3"/>
    </g>
    <text class="label" x="0" y="35">IT Security</text>
  </g>

  <!-- Backup & Recover -->
  <g class="service-node" transform="translate(489 977)">
    <circle r="78" fill="url(#node-rim)" filter="url(#soft)"/>
    <circle class="node-face" r="60"/>
    <g class="icon" transform="translate(0 -25)">
      <rect x="-22" y="-22" width="20" height="12"/>
      <rect x="-22" y="-10" width="20" height="12"/>
      <rect x="-22" y="2" width="20" height="12"/>
      <path d="M-18 -16 h6 M-18 -4 h6 M-18 8 h6 M-16 14 v6 h12 v-6"/>
      <circle cx="10" cy="0" r="12"/>
      <path d="M4 -4 a7 7 0 1 1 2 9"/>
      <path d="M2 -9 l2 5 l5 -2"/>
    </g>
    <text class="label" x="0" y="20">Backup &amp;</text>
    <text class="label" x="0" y="35">Recover</text>
  </g>

  <!-- Remote Monitoring -->
  <g class="service-node" transform="translate(308 858)">
    <circle r="78" fill="url(#node-rim)" filter="url(#soft)"/>
    <circle class="node-face" r="60"/>
    <g class="icon" transform="translate(0 -20)">
      <rect x="-20" y="-18" width="40" height="28" rx="1"/>
      <rect x="-17" y="-15" width="34" height="22"/>
      <path d="M0 10 v5 M-7 15 h14"/>
      <path d="M-12 5 v-4 M-6 5 v-7 M0 5 v-5 M6 5 v-9 M12 5 v-11"/>
      <path d="M-13 -3 l6 -4 l6 2 l6 -5 l7 -2"/>
    </g>
    <text class="label" x="0" y="20">Remote</text>
    <text class="label" x="0" y="35">Monitoring</text>
  </g>

  <!-- Networking Connectivity & Support -->
  <g class="service-node" transform="translate(219 665)">
    <circle r="78" fill="url(#node-rim)" filter="url(#soft)"/>
    <circle class="node-face" r="60"/>
    <g class="icon" transform="translate(0 -27)">
      <path d="M0 -18 L-14 -10 L-20 4 L-10 14 L4 18 L16 10 L20 -4 L12 -14 Z"/>
      <path d="M0 -18 L0 0 L-20 4 M0 0 L20 -4 M0 0 L-10 14 M0 0 L16 10 M-14 -10 L0 0 L12 -14"/>
      <circle cx="0" cy="-18" r="2.5"/><circle cx="-14" cy="-10" r="2.5"/><circle cx="12" cy="-14" r="2.5"/>
      <circle cx="-20" cy="4" r="2.5"/><circle cx="20" cy="-4" r="2.5"/><circle cx="0" cy="0" r="3"/>
      <circle cx="-10" cy="14" r="2.5"/><circle cx="16" cy="10" r="2.5"/><circle cx="4" cy="18" r="2.5"/>
    </g>
    <text class="label" x="0" y="13">Networking</text>
    <text class="label" x="0" y="28">Connectivity</text>
    <text class="label" x="0" y="43">&amp; Support</text>
  </g>

  <!-- Server Support & Administration -->
  <g class="service-node" transform="translate(247 438)">
    <circle r="78" fill="url(#node-rim)" filter="url(#soft)"/>
    <circle class="node-face" r="60"/>
    <g class="icon" transform="translate(0 -21)">
      <rect x="-22" y="-20" width="24" height="13"/>
      <rect x="-22" y="-7" width="24" height="13"/>
      <rect x="-22" y="6" width="24" height="13"/>
      <path d="M-7 -14 l-1 3 M-4 -14 l-1 3 M-1 -14 l-1 3 M-7 -1 l-1 3 M-4 -1 l-1 3 M-1 -1 l-1 3 M-7 12 l-1 3 M-4 12 l-1 3 M-1 12 l-1 3"/>
      <path d="M9 -12 v4 M9 -8 v22 q0 3 -1.5 3 q-1.5 0 -1.5 -3 v-14"/>
      <path d="M17 -14 v5 q0 3 3 3 q3 0 3 -3 v-5 M20 -6 v20"/>
    </g>
    <text class="label" x="0" y="23">Server Support &amp;</text>
    <text class="label" x="0" y="38">Administration</text>
  </g>

  <!-- Training -->
  <g class="service-node" transform="translate(385 281)">
    <circle r="78" fill="url(#node-rim)" filter="url(#soft)"/>
    <circle class="node-face" r="60"/>
    <g class="icon" transform="translate(0 -22)">
      <rect x="-10" y="-20" width="32" height="24"/>
      <path d="M12 -14 h6"/>
      <circle cx="-18" cy="-15" r="3.5"/>
      <path d="M-22 8 v-16 q0 -3 4 -3 l8 -2 l10 -4 M-14 8 v-10"/>
      <circle cx="-1" cy="8" r="4"/><circle cx="13" cy="8" r="4"/>
      <path d="M-8 20 q0 -7 7 -7 q7 0 7 7 M6 20 q0 -7 7 -7 q7 0 7 7"/>
    </g>
    <text class="label" x="0" y="33">Training</text>
  </g>
</svg>
</div>
</body>
</html>
```